20 year old business card needs re-design

We need to redesign our corporate business card look. We need something that appears more modern, eye catchy but professional.

Target Market(s)

manufacturing industry

Industry/Entity Type

Manufacturer

Contact Information for Business Card

One side can have the logo. Other side can have contact information.

Font styles to use
Serif

Colors
3277b5
33b8a4
ffffff

Requirements
Must have
• Eye catchy - need to standout from the crowd. company logo cannot change. Full name, job title, phone number and email address.
Should not have
• Fax, business address is not necessary.

```html
<!DOCTYPE html>
<html lang="en">
<head>
<meta charset="utf-8">
<title>Norvale Industrial – Business Card</title>
<link href="https://fonts.googleapis.com/css2?family=Libre+Baskerville:wght@700&family=Roboto:wght@400;700&display=swap" rel="stylesheet">
<style>
  :root {
    --backdrop: #3a3a3c;
    --card: #f4f4f4;
    --brand-blue: #0d4fa6;
    --brand-teal: #2fae9a;
    --ink: #222222;
    --ink-soft: #4a4a4a;
    --white: #ffffff;
  }
  * { margin: 0; padding: 0; box-sizing: border-box; }
  html, body {
    width: 1200px; height: 834px; overflow: hidden;
    background: var(--backdrop);
    font-family: "Roboto", Arial, sans-serif;
  }
  .canvas { position: relative; width: 1200px; height: 834px; }
  .card {
    position: absolute; width: 540px; height: 309px;
    background: linear-gradient(135deg, #fbfbfb, #e9e9e9);
    overflow: hidden;
    box-shadow: 0 14px 30px rgba(0,0,0,.45);
  }
  .card--front { left: 50px; top: 120px; }
  .card--back  { left: 610px; top: 405px; }

  .wordmark { display: flex; align-items: center; gap: 10px; color: var(--ink); font-weight: 700; }
  .wordmark__square { width: 22px; height: 22px; background: var(--brand-blue); }
  .wordmark__name { font-size: 32px; letter-spacing: -.5px; }

  .card--front .wordmark { position: absolute; left: 0; right: 0; top: 78px; justify-content: center; }

  .tagline-band {
    position: absolute; left: 0; right: 0; top: 190px; height: 70px;
    background: var(--brand-blue); color: var(--white);
    display: flex; align-items: center; justify-content: center; text-align: center;
    font-size: 13px; line-height: 1.35;
  }

  .card--back .wordmark { position: absolute; left: 40px; top: 140px; }
  .card--back .wordmark__name { font-size: 28px; }

  .contact { position: absolute; left: 300px; top: 52px; }
  .contact__name { font-family: "Libre Baskerville", Georgia, serif; font-weight: 700; font-size: 15px; color: var(--ink); }
  .contact__title { font-size: 11px; color: var(--brand-teal); margin-bottom: 14px; }
  .contact__list { list-style: none; }
  .contact__item { display: flex; align-items: center; gap: 10px; font-size: 12px; color: var(--ink-soft); margin-bottom: 7px; }
  .contact__item svg { width: 14px; height: 14px; flex: none; }

  .accent-line { position: absolute; left: 0; right: 0; bottom: 46px; height: 6px; background: var(--brand-teal); }
  .footer-band { position: absolute; left: 0; right: 0; bottom: 0; height: 46px; background: var(--brand-blue); }
</style>
</head>
<body>
<main class="canvas">
  <section class="card card--front">
    <div class="wordmark">
      <span class="wordmark__square"></span>
      <span class="wordmark__name">Norvale Industrial</span>
    </div>
    <div class="tagline-band">
      <p>International Manufacturing Solutions for OEM<br>customers in North America</p>
    </div>
  </section>

  <section class="card card--back">
    <div class="wordmark">
      <span class="wordmark__square"></span>
      <span class="wordmark__name">Norvale Industrial</span>
    </div>
    <div class="contact">
      <p class="contact__name">Sam Keller</p>
      <p class="contact__title">President</p>
      <ul class="contact__list">
        <li class="contact__item">
          <svg viewBox="0 0 24 24" fill="none" stroke="#2fae9a" stroke-width="2"><path d="M5 3h4l2 5-2.5 1.5a11 11 0 0 0 6 6L16 13l5 2v4a2 2 0 0 1-2 2A17 17 0 0 1 3 5a2 2 0 0 1 2-2z"/></svg>
          <span>555-014-2200 x120</span>
        </li>
        <li class="contact__item">
          <svg viewBox="0 0 24 24" fill="none" stroke="#2fae9a" stroke-width="2"><rect x="3" y="5" width="18" height="14"/><path d="M3 5l9 8 9-8"/></svg>
          <span>sam@norvaleindustrial.com</span>
        </li>
        <li class="contact__item">
          <svg viewBox="0 0 24 24" fill="none" stroke="#2fae9a" stroke-width="2"><circle cx="12" cy="12" r="9"/><path d="M3 12h18M12 3c3 3 3 15 0 18M12 3c-3 3-3 15 0 18"/></svg>
          <span>www.norvaleindustrial.com</span>
        </li>
      </ul>
    </div>
    <div class="accent-line"></div>
    <div class="footer-band"></div>
  </section>
</main>
</body>
</html>
```